5-6 page Website Design- Harbor Lantern Program, including 2 videos

We need an elegantly simple and beautiful website for the Harbor Lantern Program (HLP), a 6-month program for founders and leaders of startups who want to shift from Actors to Authors in their leadership.
At a minimum, the website will include:
Home Page
Program Description--Why Actor to Author?
Program Timeline and Structure
Testimonials and Past Clients (this page will include a testimonials video and text)
Team
FAQs
I'd like to see two versions of The Home Page/Landing Page:
1. Just an image with the words
If your startup is growing rapidly,
we can help you do the same.
HLP: The ACTOR to AUTHOR Shift
2. A place for a video describing the program
No payment integration on the website. Just information.
Startup founders and senior leaders

```html
<!DOCTYPE html>
<html lang="en">
<head>
<meta charset="utf-8">
<title>Harbor Lantern Program – Website Design</title>
<link href="https://fonts.googleapis.com/css2?family=Montserrat:wght@500;600;700&family=Roboto:wght@400;500;700&display=swap" rel="stylesheet">
<style>
:root{
  --board:#c8c9cb;
  --blue:#1565c0;
  --blue-bright:#1e88e5;
  --blue-soft:#2a8fd8;
  --ink:#1d1d1f;
  --muted:#666a70;
  --panel:#eef0f3;
  --footer:#141417;
  --white:#ffffff;
}
*{box-sizing:border-box;margin:0;padding:0}
html,body{width:683px;height:1200px;overflow:hidden;background:var(--board)}
body{font-family:"Roboto",Arial,sans-serif;color:var(--ink)}
.board{position:absolute;left:2.6px;top:0;width:1456px;height:2578px;transform:scale(0.46548);transform-origin:0 0}
.page{position:absolute;width:548px;background:var(--white);overflow:hidden}
.page--home{left:128px;top:141px;height:2275px}
.page--landing{left:780px;top:141px;height:509px}
.page--description{left:780px;top:775px;height:1008px}
.abs{position:absolute}
.photo{position:absolute}
.heading{font-family:"Montserrat",Arial,sans-serif;font-weight:600;color:var(--ink);letter-spacing:.2px}

/* brand */
.brand{position:absolute;display:flex;align-items:center;gap:5px}
.brand__dot{width:24px;height:24px;border-radius:50%;background:var(--blue);flex:none}
.brand__name{font-family:"Montserrat",Arial,sans-serif;font-weight:600;font-size:6.5px;line-height:7.5px;color:var(--blue-bright);text-transform:uppercase;width:58px}

/* header */
.topbar{position:absolute;left:0;top:0;width:548px;height:40px;background:var(--white)}
.contact-chip{position:absolute;top:10px;display:flex;align-items:center;gap:6px}
.contact-chip__icon{width:16px;height:16px;border-radius:50%;background:var(--blue);display:flex;align-items:center;justify-content:center}
.contact-chip__label{font-size:4.8px;color:var(--muted)}
.contact-chip__value{font-size:7px;font-weight:700;color:var(--ink)}
.nav{position:absolute;left:0;top:40px;width:548px;height:18px;background:var(--blue);display:flex;align-items:center;padding-left:42px}
.nav a{font-size:5.6px;font-weight:700;color:var(--white);text-decoration:none;text-transform:uppercase;padding:0 6px;height:18px;line-height:18px}
.nav a.is-active{background:var(--blue-bright)}

/* buttons */
.btn{position:absolute;height:21px;border-radius:11px;background:linear-gradient(90deg,var(--blue),var(--blue-bright));color:var(--white);font-size:6px;font-weight:700;display:flex;align-items:center;justify-content:center;gap:4px;text-transform:uppercase}
.btn--light{background:var(--white);color:var(--blue)}
.btn i{width:6px;height:6px;border-radius:50%;background:currentColor;display:inline-block}

/* cards */
.card{position:absolute;width:141px;height:167px;background:var(--white);box-shadow:0 1px 4px rgba(0,0,0,.15)}
.card__photo{position:absolute;left:3px;top:3px;width:135px;height:99px}
.card__title{position:absolute;left:8px;top:111px;font-size:7px;font-weight:700}
.ticks{position:absolute;left:8px;top:126px;list-style:none}
.ticks li{font-size:5.3px;color:#555;line-height:11px;padding-left:10px;position:relative}
.ticks li::before{content:"✓";position:absolute;left:0;top:2px;width:6px;height:6px;border-radius:50%;background:var(--blue-bright);color:var(--white);font-size:4px;line-height:6px;text-align:center}
.ticks--light li{color:var(--white);font-size:5.6px;line-height:11.3px;text-align:justify}
.ticks--light li::before{background:var(--white);color:var(--blue)}

.body-copy{font-size:5.9px;line-height:11.6px;color:#555;text-align:justify}
.section-title{font-family:"Montserrat",Arial,sans-serif;font-weight:600;font-size:15px;position:absolute;text-align:center;left:0;right:0}
.section-sub{font-size:5.8px;position:absolute;text-align:center;left:0;right:0;color:var(--ink)}
.module-title{position:absolute;left:0;right:0;text-align:center;font-size:14px;font-weight:500;color:var(--blue)}

/* testimonials */
.video{position:absolute;width:216px;height:121px}
.play{position:absolute;left:98px;top:52px;width:20px;height:14px;border-radius:3px;background:#e52020}
.play::after{content:"";position:absolute;left:8px;top:4px;border-left:5px solid var(--white);border-top:3px solid transparent;border-bottom:3px solid transparent}
.quote{position:absolute;width:193px;height:88px;background:var(--white);box-shadow:0 2px 6px rgba(0,0,0,.14);padding:12px 18px 0}
.quote p{font-size:5.8px;line-height:11.4px;text-align:center;color:#555}
.quote__mark{position:absolute;font-family:Georgia,serif;font-size:16px;font-weight:700;color:var(--blue);line-height:16px}
.quote__brand{position:absolute;left:0;right:0;bottom:9px;text-align:center;font-size:6.5px;font-weight:700;color:var(--ink)}

/* team */
.member{position:absolute;width:130px;text-align:center}
.member__photo{width:74px;height:74px;border-radius:50%;border:2px solid var(--blue-bright);margin:0 auto;background:linear-gradient(160deg,#cfd6de,#7d8794)}
.member__name{font-size:7.5px;font-weight:700;margin-top:10px}
.member__role{font-size:4.6px;color:var(--muted);margin-top:1px}
.member__bio{font-size:5.8px;line-height:11px;color:#555;margin-top:7px}

/* footer */
.footer{position:absolute;left:0;width:548px;height:170px;background:var(--footer);color:var(--white)}
.footer__col{position:absolute;top:28px}
.footer__head{font-size:7px;font-weight:700;text-transform:uppercase;padding-bottom:6px;position:relative}
.footer__head::after{content:"";position:absolute;left:0;bottom:0;width:26px;height:1px;background:var(--blue-bright)}
.footer__links{list-style:none;margin-top:11px}
.footer__links li{font-size:4.9px;line-height:11.6px;color:#d8d8dc}
.footer__contact{list-style:none;margin-top:13px}
.footer__contact li{font-size:4.9px;line-height:9.5px;color:#d8d8dc;padding-left:16px;position:relative;margin-bottom:9px}
.footer__contact svg{position:absolute;left:3px;top:2px}
.footer__text{font-size:4.9px;line-height:9.5px;color:#d8d8dc;margin-top:12px;width:110px}
.subscribe{display:flex;margin-top:6px}
.subscribe__field{width:93px;height:16px;background:var(--white);border-radius:8px 0 0 8px;font-size:4.5px;color:#888;padding-left:7px;line-height:16px}
.subscribe__send{width:22px;height:16px;background:var(--blue-bright);border-radius:0 8px 8px 0;display:flex;align-items:center;justify-content:center}
.socials{position:absolute;left:61px;top:95px;display:flex;gap:6px}
.socials span{width:12px;height:12px;border-radius:50%;background:var(--white)}
.footer__bottom{position:absolute;left:50px;right:50px;top:152px;font-size:5.2px;color:#d8d8dc;display:flex;justify-content:space-between}
.footer__bottom u{color:var(--white)}

/* hero extras */
.hamburger{position:absolute;width:9px;height:7px;border-top:1.5px solid #111;border-bottom:1.5px solid #111}
.hamburger::after{content:"";position:absolute;left:0;right:0;top:1.3px;height:1.5px;background:#111}
.centered-copy{position:absolute;left:54px;width:440px;text-align:center;font-size:5.7px;line-height:12.6px;color:#555}
.centered-copy p{margin-bottom:4px}
.centered-copy strong{color:var(--ink);font-size:6.6px}
</style>
</head>
<body>
<div class="board">

  <!-- ============ HOME PAGE ============ -->
  <section class="page page--home">
    <header class="topbar">
      <div class="brand" style="left:50px;top:8px"><span class="brand__dot"></span><span class="brand__name">Harbor Lantern Program</span></div>
      <div class="contact-chip" style="left:250px">
        <span class="contact-chip__icon"><svg width="8" height="6" viewBox="0 0 8 6"><rect x=".5" y=".5" width="7" height="5" fill="none" stroke="#fff"/><path d="M.5 .5 4 3.3 7.5 .5" fill="none" stroke="#fff"/></svg></span>
        <div><div class="contact-chip__label">Email us on</div><div class="contact-chip__value">info@harborlanternprogram.com</div></div>
      </div>
      <div class="contact-chip" style="left:410px">
        <span class="contact-chip__icon"><svg width="8" height="8" viewBox="0 0 8 8"><path d="M1.5 .8 3 2.6 2.3 3.5Q3.3 5 4.6 5.8L5.5 5 7.2 6.5 6.4 7.4Q3.5 7 .7 2.2Z" fill="#fff"/></svg></span>
        <div><div class="contact-chip__label">Call or text us</div><div class="contact-chip__value">+1 (555) 010 2040</div></div>
      </div>
    </header>
    <nav class="nav">
      <a class="is-active">Home</a><a>Program Description</a><a>Program Timeline and Structure</a><a>Testimonials and Past Clients</a><a>Team</a><a>FAQs</a><a>Contact</a>
    </nav>

    <div class="photo" role="img" aria-label="Hiker sitting on a mountain top with arms raised at sunset" style="left:0;top:58px;width:548px;height:311px;background:linear-gradient(180deg,#e6b47c 0%,#d98a5a 22%,#8a6fa0 48%,#4f5a8c 72%,#3a3f6a 100%)"></div>
    <svg class="abs" style="left:0;top:58px" width="548" height="311" viewBox="0 0 548 311">
      <path d="M0 238 Q274 380 548 236 L548 311 L0 311Z" fill="#fff"/>
      <path d="M0 238 Q274 380 548 236" fill="none" stroke="var(--blue-bright)" stroke-width="4"/>
    </svg>
    <h1 class="heading abs" style="left:51px;top:73px;font-size:17px;line-height:22px;color:#fff;text-transform:uppercase;width:230px">Harbor Lantern Program</h1>
    <p class="abs" style="left:51px;top:124px;width:232px;font-size:6.3px;line-height:12.5px;color:#fff">If you want to be busy and anxious, practice busy anxiousness. If you want to be calm and centered, practice it.</p>
    <div class="btn" style="left:51px;top:164px;width:94px">Get Started <i></i></div>

    <!-- description -->
    <div class="abs" style="left:51px;top:396px;width:206px;height:206px;border-radius:50%;background:var(--blue);display:flex;align-items:center;justify-content:center">
      <span style="font-family:Montserrat,sans-serif;font-weight:600;font-size:12px;color:#fff;text-align:center;width:140px;text-transform:uppercase;line-height:15px">Harbor Lantern Program</span>
    </div>
    <h2 class="heading abs" style="left:289px;top:416px;font-size:15px">PROGRAM DESCRIPTION</h2>
    <div class="body-copy abs" style="left:290px;top:443px;width:208px">
      <p>"If you want to be busy and anxious, practice busy anxiousness. If you want to be calm and centered, practice it. It's as simple as that." (Mara Ellison, Westbrook mindfulness teacher and researcher)</p>
      <p>Well thanks Mara, sounds pretty simple...but what about when I've got 11 back-to-back meetings, a board meeting to prepare for with investors who have sky-high expectations, 6 new hires to onboard and 16 more to find, and–not least–a product to improve for the customers we are trying to serve and retain–only to wake up,</p>
    </div>
    <div class="btn" style="left:290px;top:555px;width:80px;height:20px">Read More <i></i></div>

    <!-- timeline -->
    <section class="abs" style="left:0;top:637px;width:548px;height:580px;background:var(--panel)">
      <h2 class="section-title" style="top:27px">PROGRAM TIMELINE AND STRUCTURE</h2>
      <p class="section-sub" style="top:47px">Everything will be virtual except the 2 retreats (with strict COVID protocols)</p>
      <h3 class="module-title" style="top:73px">Leading Yourself</h3>

      <article class="card" style="left:51px;top:102px"><div class="card__photo" role="img" aria-label="Person meditating on a misty beach" style="background:linear-gradient(180deg,#d9dfe4,#b7b1a8)"></div><div class="card__title">Month 1</div><ul class="ticks"><li>Week 1: Kickoff Orientation Workshop</li><li>Week 2: 1on1 Exec Coaching Session</li><li>Week 3: Workshop</li></ul></article>
      <article class="card" style="left:204px;top:102px"><div class="card__photo" role="img" aria-label="Woman meditating at a desk with laptop" style="background:linear-gradient(180deg,#e8e4de,#8a7a62)"></div><div class="card__title">Month 1</div><ul class="ticks"><li>Week 1: Kickoff Orientation Workshop</li><li>Week 2: 1on1 Exec Coaching Session</li><li>Week 3: Workshop</li></ul></article>
      <article class="card" style="left:356px;top:102px"><div class="card__photo" role="img" aria-label="Woman in white meditating by a lake" style="background:linear-gradient(180deg,#8fa6bd,#3f5f7f)"></div><div class="card__title">Month 1</div><ul class="ticks"><li>Week 1: Kickoff Orientation Workshop</li><li>Week 2: 1on1 Exec Coaching Session</li><li>Week 3: Workshop</li></ul></article>

      <h3 class="module-title" style="top:298px">Leading Relationships, Leading Others</h3>
      <article class="card" style="left:51px;top:328px"><div class="card__photo" role="img" aria-label="Person on a beach reaching out a hand" style="background:linear-gradient(180deg,#c7d3db,#9b8f80)"></div><div class="card__title">Month 1</div><ul class="ticks"><li>Week 1: Kickoff Orientation Workshop</li><li>Week 2: 1on1 Exec Coaching Session</li><li>Week 3: Workshop</li></ul></article>
      <article class="card" style="left:204px;top:328px"><div class="card__photo" role="img" aria-label="Woman standing in a turquoise mountain lake" style="background:linear-gradient(180deg,#6e8ba6,#2fb0bf)"></div><div class="card__title">Month 1</div><ul class="ticks"><li>Week 1: Kickoff Orientation Workshop</li><li>Week 2: 1on1 Exec Coaching Session</li><li>Week 3: Workshop</li></ul></article>
      <article class="card" style="left:356px;top:328px"><div class="card__photo" role="img" aria-label="Woman meditating indoors on a mat" style="background:linear-gradient(180deg,#e6e4e0,#9a4a6a)"></div><div class="card__title">Month 1</div><ul class="ticks"><li>Week 1: Kickoff Orientation Workshop</li><li>Week 2: 1on1 Exec Coaching Session</li><li>Week 3: Workshop</li></ul></article>
    </section>

    <!-- logic -->
    <svg class="abs" style="left:0;top:1180px" width="548" height="340" viewBox="0 0 548 340">
      <defs><linearGradient id="logicFill" x1="0" x2="1"><stop offset="0" stop-color="#1558b0"/><stop offset="1" stop-color="#2a93dc"/></linearGradient></defs>
      <path d="M0 335 L0 64 Q274 -56 548 64 L548 335Z" fill="#fff"/>
      <path d="M0 64 Q274 -56 548 64 L548 270 Q274 395 0 270Z" fill="url(#logicFill)"/>
    </svg>
    <h2 class="section-title" style="top:1222px;color:#fff">THE LOGIC BEHIND THE STRUCTURE</h2>
    <p class="section-sub" style="top:1242px;color:#fff">Why combine both group format (retreats/workshops) and 1on1 exec coaching?</p>
    <h3 class="heading abs" style="left:51px;top:1280px;font-size:12px;color:#fff">WHY RETREATS? IMMERSION!</h3>
    <ul class="ticks ticks--light" style="left:51px;top:1307px;width:208px">
      <li>The retreat environment creates an immersive experience, co-created by the group. The sharp distinction from the fast pace of everyday startup life helps participants stand outside their everyday habits and evaluate which ones they want to change. Furthermore, just like in learning a language, immersion is the most powerful context for learning and ingraining new habits.</li>
      <li style="margin-top:5px">Even so, we are wary of the format taken by many retreats/bootcamps which focus on just this one-off peak experience, neither sowing the seeds</li>
    </ul>
    <div class="btn btn--light" style="left:51px;top:1431px;width:80px;height:20px">Read More <i></i></div>
    <div class="photo" role="img" aria-label="Woman meditating outdoors facing the sunset" style="left:294px;top:1271px;width:202px;height:202px;border-radius:50%;background:radial-gradient(circle at 60% 35%,#f7d79a 0%,#e39a52 30%,#6b4a3c 70%,#2d2722 100%)"></div>

    <!-- testimonials -->
    <h2 class="section-title" style="top:1547px">TESTIMONIALS AND PAST CLIENTS</h2>
    <div class="video" role="img" aria-label="Video still of a woman meditating on a beach at sunset" style="left:51px;top:1581px;background:linear-gradient(180deg,#f2b466,#c8713e 55%,#6e4a3a)"><span class="play"></span></div>
    <div class="video" role="img" aria-label="Video still of a woman breathing calmly in a dark forest" style="left:281px;top:1581px;background:linear-gradient(180deg,#2e3a36,#4b4a48 60%,#7b7772)"><span class="play"></span></div>
    <div class="quote" style="left:63px;top:1694px"><span class="quote__mark" style="left:6px;top:4px">“</span><p>Lorem ipsum dolor sit amet, consectetur adipiscing elit, sed do eiusmod tempor incididunt ut labore et dolore magna aliqua. Ut enim ad minim veniam, quis aliquip ex ea commodo consequat.</p><span class="quote__mark" style="right:30px;top:48px">”</span><div class="quote__brand">Northfield</div></div>
    <div class="quote" style="left:293px;top:1694px"><span class="quote__mark" style="left:6px;top:4px">“</span><p>Lorem ipsum dolor sit amet, consectetur adipiscing elit, sed do eiusmod tempor incididunt ut labore et dolore magna aliqua. Ut enim ad minim veniam, quis aliquip ex ea commodo consequat.</p><span class="quote__mark" style="right:30px;top:48px">”</span><div class="quote__brand">Northfield</div></div>

    <!-- team -->
    <section class="abs" style="left:0;top:1826px;width:548px;height:330px;background:var(--panel)">
      <h2 class="section-title" style="top:26px">OUR TEAM</h2>
      <div class="member" style="left:48px;top:60px"><div class="member__photo" role="img" aria-label="Portrait of a team member in a suit"></div><div class="member__name">JOHN DOE</div><div class="member__role">Director</div><p class="member__bio">Lorem ipsum dolor sit amet, consectetur adipiscing elit, sed do eiusmod tempor ut labore et dolore magna aliqua.</p></div>
      <div class="member" style="left:209px;top:60px"><div class="member__photo" role="img" aria-label="Portrait of a team member in a grey jacket"></div><div class="member__name">JOHN DOE</div><div class="member__role">Director</div><p class="member__bio">Lorem ipsum dolor sit amet, consectetur adipiscing elit, sed do eiusmod tempor ut labore et dolore magna aliqua.</p></div>
      <div class="member" style="left:370px;top:60px"><div class="member__photo" role="img" aria-label="Portrait of a bearded team member"></div><div class="member__name">JOHN DOE</div><div class="member__role">Director</div><p class="member__bio">Lorem ipsum dolor sit amet, consectetur adipiscing elit, sed do eiusmod tempor ut labore et dolore magna aliqua.</p></div>
    </section>
    <svg class="abs" style="left:0;top:2064px" width="548" height="50" viewBox="0 0 548 50">
      <path d="M0 76 Q274 -40 548 76Z" fill="var(--footer)"/>
      <path d="M0 74 Q274 -44 548 74" fill="none" stroke="var(--blue-bright)" stroke-width="4"/>
    </svg>
    <footer class="footer" style="top:2105px">
      <div class="brand" style="left:50px;top:46px"><span class="brand__dot"></span><span class="brand__name">Harbor Lantern Program</span></div>
      <div class="socials"><span></span><span></span><span></span><span></span></div>
      <div class="footer__col" style="left:169px"><div class="footer__head">Quick Links</div><ul class="footer__links"><li>Home</li><li>Program Description</li><li>Program Timeline and Structure</li><li>Testimonials and Past Clients</li><li>Team</li><li>FAQs</li></ul></div>
      <div class="footer__col" style="left:270px"><div class="footer__head">Contact Us</div><ul class="footer__contact"><li><svg width="6" height="6" viewBox="0 0 8 8"><path d="M1.5 .8 3 2.6 2.3 3.5Q3.3 5 4.6 5.8L5.5 5 7.2 6.5 6.4 7.4Q3.5 7 .7 2.2Z" fill="#fff"/></svg>0300 555 0142</li><li><svg width="6" height="5" viewBox="0 0 8 6"><rect width="8" height="6" fill="#fff"/></svg>info@northwind-studio.com</li><li><svg width="5" height="7" viewBox="0 0 6 8"><path d="M3 8 .5 4A2.6 2.6 0 1 1 5.5 4Z" fill="#fff"/></svg>Unit 7 Mill Lane<br>Farley, FR2 4QT</li><li><svg width="6" height="6" viewBox="0 0 6 6"><rect width="6" height="6" rx="1" fill="#fff"/></svg>0300 555 0142</li></ul></div>
      <div class="footer__col" style="left:382px"><div class="footer__head">Subscribe to our Blog</div><p class="footer__text">Sign up today to get resources on how to attract and retain more customers!</p><div class="subscribe"><span class="subscribe__field">Email Address</span><span class="subscribe__send"><svg width="7" height="7" viewBox="0 0 8 8"><path d="M0 3.5 8 0 5 8 3.8 4.5Z" fill="#fff"/></svg></span></div></div>
      <div class="footer__bottom"><span>Copyright© 2022 <u>Harbor Lantern program</u> | All Rights Reserved</span><span>Terms and Conditions | Privacy Policy | Site Map</span></div>
    </footer>
  </section>

  <!-- ============ LANDING VERSION ============ -->
  <section class="page page--landing">
    <div class="photo" role="img" aria-label="Woman in a white dress with arms raised on a mountain at sunset" style="left:0;top:0;width:548px;height:339px;background:linear-gradient(180deg,#f1d8b0 0%,#e9b47a 30%,#b86a3a 55%,#5a3222 80%,#2e2018 100%)"></div>
    <div class="brand" style="left:52px;top:22px"><span class="brand__dot"></span><span class="brand__name">Harbor Lantern Program</span></div>
    <span class="hamburger" style="left:487px;top:33px"></span>
    <span class="abs" style="left:52px;top:147px;width:2px;height:103px;background:#fff"></span>
    <span class="abs" style="left:52px;top:248px;width:40px;height:2px;background:#fff"></span>
    <h1 class="heading abs" style="left:69px;top:162px;width:250px;font-size:18.5px;line-height:23px;color:#fff">If your startup is growing rapidly,we can help you do the same.</h1>
    <p class="abs" style="left:102px;top:244px;font-size:7px;font-weight:700;color:#fff">HLP: The ACTOR to AUTHOR Shift</p>
    <footer class="footer" style="top:339px">
      <div class="brand" style="left:50px;top:46px"><span class="brand__dot"></span><span class="brand__name">Harbor Lantern Program</span></div>
      <div class="socials"><span></span><span></span><span></span><span></span></div>
      <div class="footer__col" style="left:169px"><div class="footer__head">Quick Links</div><ul class="footer__links"><li>Home</li><li>Program Description</li><li>Program Timeline and Structure</li><li>Testimonials and Past Clients</li><li>Team</li><li>FAQs</li></ul></div>
      <div class="footer__col" style="left:270px"><div class="footer__head">Contact Us</div><ul class="footer__contact"><li><svg width="6" height="6" viewBox="0 0 8 8"><path d="M1.5 .8 3 2.6 2.3 3.5Q3.3 5 4.6 5.8L5.5 5 7.2 6.5 6.4 7.4Q3.5 7 .7 2.2Z" fill="#fff"/></svg>0300 555 0142</li><li><svg width="6" height="5" viewBox="0 0 8 6"><rect width="8" height="6" fill="#fff"/></svg>info@northwind-studio.com</li><li><svg width="5" height="7" viewBox="0 0 6 8"><path d="M3 8 .5 4A2.6 2.6 0 1 1 5.5 4Z" fill="#fff"/></svg>Unit 7 Mill Lane<br>Farley, FR2 4QT</li><li><svg width="6" height="6" viewBox="0 0 6 6"><rect width="6" height="6" rx="1" fill="#fff"/></svg>0300 555 0142</li></ul></div>
      <div class="footer__col" style="left:382px"><div class="footer__head">Subscribe to our Blog</div><p class="footer__text">Sign up today to get resources on how to attract and retain more customers!</p><div class="subscribe"><span class="subscribe__field">Email Address</span><span class="subscribe__send"><svg width="7" height="7" viewBox="0 0 8 8"><path d="M0 3.5 8 0 5 8 3.8 4.5Z" fill="#fff"/></svg></span></div></div>
      <div class="footer__bottom"><span>Copyright© 2022 <u>Harbor Lantern program</u> | All Rights Reserved</span><span>Terms and Conditions | Privacy Policy | Site Map</span></div>
    </footer>
  </section>

  <!-- ============ PROGRAM DESCRIPTION PAGE ============ -->
  <section class="page page--description">
    <div class="photo" role="img" aria-label="Woman with arms open breathing in a sunlit meadow" style="left:0;top:30px;width:548px;height:287px;background:linear-gradient(180deg,#f3e6cf 0%,#e8a356 25%,#a8652c 55%,#4d5a2a 80%,#2f3a1c 100%)"></div>
    <div class="abs" style="left:0;top:0;width:548px;height:44px;background:linear-gradient(180deg,#fff 70%,rgba(255,255,255,0))"></div>
    <div class="brand" style="left:52px;top:10px"><span class="brand__dot"></span><span class="brand__name">Harbor Lantern Program</span></div>
    <span class="hamburger" style="left:487px;top:25px"></span>
    <span class="abs" style="left:54px;top:127px;width:22px;height:22px;border-radius:50%;background:var(--blue-bright)"></span>
    <span class="abs" style="left:63px;top:133px;border-left:7px solid #fff;border-top:5px solid transparent;border-bottom:5px solid transparent"></span>
    <h1 class="heading abs" style="left:49px;top:160px;font-size:19px;color:#fff">Program Description</h1>
    <p class="abs" style="left:52px;top:192px;width:268px;font-size:6.5px;line-height:12.5px;color:#fff">"If you want to be busy and anxious, practice busy anxiousness. If you want to be calm and centered, practice it. It's as simple as that."</p>

    <span class="abs" style="left:257px;top:340px;width:34px;height:34px;border-radius:50%;background:var(--blue)"></span>
    <div class="centered-copy" style="top:384px">
      <p>Well thanks Mara, sounds pretty simple...but what about when I've got 11 back-to-back meetings, a board meeting to prepare for with investors who have sky-high expectations, 6 new hires to onboard and 16 more to find, and–not least–a product to improve for the customers we are trying to serve and retain–only to wake up, rinse (maybe) and repeat tomorrow?? (We didn't even mention the team chat and email messages mounting in the background.) How could I possibly exit "busy anxiousness" and practice calm centeredness amidst this chaos? (Notice what you feel just reading that–does your body tighten a bit?) Calm sounds nice–for vacation! I want results.</p>
      <p>There is a way, not to perfection and a stress-less existence, but rather a way of working, being, and leading from a deeper calm that creates enough space to harness the remaining (necessary) stress as fuel towards your goals.</p>
      <p><strong>We call this way Harbor Lantern.</strong></p>
      <p>We see Harbor Lantern as the key ingredient in the shift from Actor to Author. Why might it be especially relevant to you right now?<br>If your startup is growing rapidly, you're hitting (or already past) a key inflection point: expanding your focus from building a product/service to building a team and organization. It is in this formative moment that leadership is so crucial, when weaknesses–and strengths–as a leader become apparent and embed themselves as norms across the developing org.</p>
      <p>If your startup is growing rapidly, you're hitting (or already past) a key inflection point: expanding your focus from building a product/service to building a team and organization. It is in this formative moment that leadership is so crucial, when weaknesses–and strengths–as a leader become apparent and embed themselves as norms across the developing org.</p>
      <p>If you are not continually shaping your habits to optimize how you allocate your time and attention and how you lead conversations, then you are relying on outdated habits that developed in a smaller context where you were primarily responsible for making the product itself. You are working only IN the organization instead of ON it as well. Simply put, you are re-acting based on an outdated script. You are missing out on opportunities to Author and Architect what's possible.</p>
      <p>How do you shift from Acting out your old role to Authoring your new one–and do so continually?</p>
      <p>On an individual level, this means creating an Operating System, a set of habits and tools that enable you to consistently define and prioritize what matters most and allocate your time and attention there systematically. Systematically means proactively instead of the ad-hoc, reactive reflexes you might be used to. Beyond habits and tools lie the Creative Mindset, a set of radically response-able ways of thinking that help you see your choice points and direct (or course-correct) your way toward what you value most.</p>
      <p>On an interpersonal level, this means shifting from reacting to what others have said and done–and what that triggers inside you–to leading the dance, using conflict and confusion as opportunities to create clarity and connection, and starting to do this proactively and preemptively too.</p>
      <p><strong>To these ends, HLP consists of two modules that each support the other:</strong></p>
      <p>1. Leading Yourself<br>2. Leading Relationships/Leading Others.</p>
    </div>
    <footer class="footer" style="top:838px">
      <div class="brand" style="left:50px;top:46px"><span class="brand__dot"></span><span class="brand__name">Harbor Lantern Program</span></div>
      <div class="socials"><span></span><span></span><span></span><span></span></div>
      <div class="footer__col" style="left:169px"><div class="footer__head">Quick Links</div><ul class="footer__links"><li>Home</li><li>Program Description</li><li>Program Timeline and Structure</li><li>Testimonials and Past Clients</li><li>Team</li><li>FAQs</li></ul></div>
      <div class="footer__col" style="left:270px"><div class="footer__head">Contact Us</div><ul class="footer__contact"><li><svg width="6" height="6" viewBox="0 0 8 8"><path d="M1.5 .8 3 2.6 2.3 3.5Q3.3 5 4.6 5.8L5.5 5 7.2 6.5 6.4 7.4Q3.5 7 .7 2.2Z" fill="#fff"/></svg>0300 555 0142</li><li><svg width="6" height="5" viewBox="0 0 8 6"><rect width="8" height="6" fill="#fff"/></svg>info@northwind-studio.com</li><li><svg width="5" height="7" viewBox="0 0 6 8"><path d="M3 8 .5 4A2.6 2.6 0 1 1 5.5 4Z" fill="#fff"/></svg>Unit 7 Mill Lane<br>Farley, FR2 4QT</li><li><svg width="6" height="6" viewBox="0 0 6 6"><rect width="6" height="6" rx="1" fill="#fff"/></svg>0300 555 0142</li></ul></div>
      <div class="footer__col" style="left:382px"><div class="footer__head">Subscribe to our Blog</div><p class="footer__text">Sign up today to get resources on how to attract and retain more customers!</p><div class="subscribe"><span class="subscribe__field">Email Address</span><span class="subscribe__send"><svg width="7" height="7" viewBox="0 0 8 8"><path d="M0 3.5 8 0 5 8 3.8 4.5Z" fill="#fff"/></svg></span></div></div>
      <div class="footer__bottom"><span>Copyright© 2022 <u>Harbor Lantern program</u> | All Rights Reserved</span><span>Terms and Conditions | Privacy Policy | Site Map</span></div>
    </footer>
  </section>

</div>
</body>
</html>
```